design a construction company business card

Design business card around our logo. Card must have all the typical info: name, title, address, phone, email, business name, etc. Somewhere on the card I would like to see our motto "Built on integrity... Inspired by commitment." Consider adding a splash of bright orange to the card to complement the blues and silvers/grays in the logo. We are open to metallic inks, textures, etc. We would like to see options on both light and dark backgrounds. The font in the logo is Euro Technic Extended Regular.

```html
<!DOCTYPE html>
<html lang="en">
<head>
<meta charset="utf-8">
<title>Halden Contracting – Business Card</title>
<link href="https://fonts.googleapis.com/css2?family=Michroma&family=Orbitron:wght@700&display=swap" rel="stylesheet">
<style>
  :root {
    --backdrop: #2a2a2b;
    --card: #1f1f20;
    --brand-blue: #2f6fd6;
    --accent-blue: #2b8be0;
    --silver: #8d8f92;
    --ink-white: #f2f2f2;
    --divider: #bdbdbd;
  }
  * { margin: 0; padding: 0; box-sizing: border-box; }
  html, body {
    width: 1200px; height: 901px; overflow: hidden;
    background: var(--backdrop);
    font-family: "Michroma", sans-serif;
  }
  .stage {
    width: 1200px; height: 901px;
    display: flex; flex-direction: column; align-items: center; justify-content: center;
    gap: 40px;
  }
  .card {
    width: 640px; height: 366px;
    background: var(--card);
    box-shadow: 0 10px 30px rgba(0,0,0,.45);
    position: relative;
  }
  /* front */
  .card-front { display: flex; flex-direction: column; align-items: center; justify-content: center; }
  .wordmark {
    display: flex; align-items: center; gap: 12px;
    font-size: 30px; letter-spacing: 2px; line-height: 1;
  }
  .wordmark-mark { width: 22px; height: 22px; }
  .wordmark-sub { font-size: 11px; letter-spacing: 3px; margin-top: 12px; text-align: center; }
  .card-front .wordmark, .card-front .wordmark-sub { color: var(--brand-blue); }
  .card-front .wordmark-mark { background: var(--brand-blue); }
  .motto {
    position: absolute; bottom: 48px; left: 0; right: 0;
    text-align: center; color: var(--accent-blue);
    font-size: 13px; letter-spacing: 1.5px;
  }
  /* back */
  .card-back { display: flex; align-items: center; padding: 0 40px; }
  .back-brand { width: 270px; display: flex; flex-direction: column; align-items: center; }
  .card-back .wordmark, .card-back .wordmark-sub { color: var(--silver); }
  .card-back .wordmark { font-size: 26px; }
  .card-back .wordmark-mark { background: var(--silver); }
  .divider { width: 1px; height: 160px; background: var(--divider); margin: 0 28px 0 12px; }
  .contact { color: var(--ink-white); }
  .contact-name { font-family: "Orbitron", sans-serif; font-weight: 700; font-size: 24px; letter-spacing: 1px; }
  .contact-title { color: var(--accent-blue); font-size: 14px; margin: 4px 0 16px; }
  .contact-address { font-size: 11.5px; line-height: 1.5; margin-bottom: 6px; }
  .contact-list { list-style: none; font-size: 12.5px; line-height: 1.75; }
  .contact-list li { display: flex; align-items: center; gap: 10px; }
  .contact-list svg { width: 11px; height: 11px; fill: var(--accent-blue); flex: none; }
  .web-domain { color: var(--accent-blue); }
</style>
</head>
<body>
<main class="stage">
  <section class="card card-front">
    <div class="wordmark"><span class="wordmark-mark"></span>HALDEN</div>
    <div class="wordmark-sub">CONTRACTING, INC.</div>
    <p class="motto">"Built on integrity... Inspired by commitment."</p>
  </section>

  <section class="card card-back">
    <div class="back-brand">
      <div class="wordmark"><span class="wordmark-mark"></span>HALDEN</div>
      <div class="wordmark-sub">CONTRACTING, INC.</div>
    </div>
    <div class="divider"></div>
    <div class="contact">
      <h1 class="contact-name">DANIEL BROOKS</h1>
      <p class="contact-title">Ceo &amp; Founder</p>
      <p class="contact-address">Your Street Address,<br>UnitedStates, 1234</p>
      <ul class="contact-list">
        <li><svg viewBox="0 0 24 24"><path d="M6.6 10.8a15 15 0 0 0 6.6 6.6l2.2-2.2c.3-.3.7-.4 1-.2 1.1.4 2.3.6 3.6.6.6 0 1 .4 1 1V20c0 .6-.4 1-1 1A17 17 0 0 1 3 4c0-.6.4-1 1-1h3.5c.6 0 1 .4 1 1 0 1.3.2 2.5.6 3.6.1.3 0 .7-.2 1z"/></svg>000 111 2223</li>
        <li><svg viewBox="0 0 24 24"><path d="M2 5h20v14H2z M4 7v.5l8 5 8-5V7l-8 5z" fill-rule="evenodd"/></svg>urname@email.com</li>
        <li><svg viewBox="0 0 24 24"><circle cx="12" cy="12" r="10"/></svg>www.<span class="web-domain">ursitename</span>.com</li>
      </ul>
    </div>
  </section>
</main>
</body>
</html>
```